Landscape design build company door flyer

I would like this flyer to convey a high-level of professionalism for a company that is excellent with communication with their clients as well as a company that does incredible installations

Went on vacation/holiday

```html
<!DOCTYPE html>
<html lang="en">
<head>
<meta charset="UTF-8">
<title>Summit Builders – Outdoor Living Spaces Flyer</title>
<link href="https://fonts.googleapis.com/css2?family=Poppins:wght@400;500;600;700;800&display=swap" rel="stylesheet">
<style>
  :root {
    --navy: #0b2a40;
    --paper: #f2f2f2;
    --stone: #cbcbcb;
    --rule: #9a9a9a;
    --ink: #111418;
    --white: #ffffff;
  }
  * { margin: 0; padding: 0; box-sizing: border-box; }
  html, body { width: 933px; height: 1200px; overflow: hidden; background: var(--paper); }
  body { font-family: "Poppins", sans-serif; color: var(--ink); }
  .flyer { position: relative; width: 933px; height: 1200px; background: var(--paper); overflow: hidden; }
  .layer { position: absolute; left: 0; top: 0; }

  .brand { position: absolute; left: 60px; top: 112px; width: 250px; text-align: center; color: var(--navy); }
  .brand-name { font-weight: 700; font-size: 22px; letter-spacing: 0.5px; line-height: 1; display: inline-flex; align-items: center; gap: 8px; }
  .brand-mark { width: 12px; height: 12px; background: var(--navy); display: inline-block; }
  .brand-tag { font-weight: 700; font-size: 9.5px; margin-top: 4px; }

  .headline { position: absolute; left: 42px; top: 238px; color: var(--white); font-weight: 700; font-size: 60px; line-height: 68px; letter-spacing: -0.5px; text-transform: uppercase; }

  .section-title { font-weight: 800; font-size: 29px; line-height: 1; letter-spacing: -0.3px; text-transform: uppercase; }
  .section-rule { width: 81px; height: 4px; background: var(--rule); margin-top: 10px; }

  .about { position: absolute; left: 42px; top: 590px; width: 395px; }
  .about p { margin-top: 14px; font-size: 14.3px; line-height: 17.8px; text-align: justify; hyphens: auto; }

  .services { position: absolute; left: 513px; top: 590px; }
  .services ul { list-style: none; margin-top: 14px; }
  .services li { display: flex; align-items: center; gap: 18px; height: 25.3px; font-weight: 500; font-size: 16.5px; }
  .services svg { width: 16px; height: 16px; flex: none; }

  .works-title { position: absolute; left: 330px; top: 842px; width: 264px; height: 35px; background: var(--navy); color: var(--white); font-weight: 800; font-size: 22px; text-align: center; line-height: 36px; }

  .contact-phone { position: absolute; left: 58px; top: 1118px; display: flex; align-items: center; gap: 14px; color: var(--white); font-weight: 700; font-size: 52px; line-height: 1; letter-spacing: -0.5px; }
  .contact-phone svg { width: 34px; height: 40px; }
  .contact-list { position: absolute; left: 610px; top: 1103px; list-style: none; color: var(--navy); }
  .contact-list li { display: flex; align-items: center; gap: 24px; height: 31px; font-size: 17px; }
  .contact-list svg { width: 20px; height: 20px; flex: none; }
</style>
</head>
<body>
<main class="flyer">
  <svg class="layer" width="933" height="1200" viewBox="0 0 933 1200" aria-hidden="false">
    <defs>
      <linearGradient id="houseTones" x1="0" y1="0" x2="1" y2="1">
        <stop offset="0" stop-color="#6b7a54"/>
        <stop offset="0.35" stop-color="#6e7378"/>
        <stop offset="0.7" stop-color="#55585a"/>
        <stop offset="1" stop-color="#4a3a2e"/>
      </linearGradient>
      <linearGradient id="deckTones" x1="0" y1="0" x2="0" y2="1">
        <stop offset="0" stop-color="#4f7a3a"/>
        <stop offset="0.5" stop-color="#8a5a3a"/>
        <stop offset="1" stop-color="#a0603a"/>
      </linearGradient>
      <linearGradient id="poolTones" x1="0" y1="0" x2="1" y2="1">
        <stop offset="0" stop-color="#3d5a34"/>
        <stop offset="0.45" stop-color="#7fc9c4"/>
        <stop offset="1" stop-color="#d8d8d6"/>
      </linearGradient>
      <linearGradient id="firepitTones" x1="0" y1="0" x2="0" y2="1">
        <stop offset="0" stop-color="#5a6a4a"/>
        <stop offset="0.5" stop-color="#6a6562"/>
        <stop offset="1" stop-color="#4a3e36"/>
      </linearGradient>
    </defs>

    <rect class="hero-photo" x="0" y="0" width="933" height="565" fill="url(#houseTones)" role="img" aria-label="Aerial photo of a home with a new paver driveway, steps and planting beds"/>
    <polygon class="brand-band" points="0,0 428,0 363,191 0,191" fill="var(--stone)"/>
    <polygon class="headline-panel" points="0,191 437,191 623,565 0,565" fill="var(--navy)"/>

    <line class="works-rule" x1="0" y1="861" x2="933" y2="861" stroke="var(--navy)" stroke-width="2"/>
    <rect x="48" y="893" width="253" height="138" fill="url(#deckTones)" role="img" aria-label="Wooden deck with pergola and patio chairs"/>
    <rect x="336" y="893" width="252" height="138" fill="url(#poolTones)" role="img" aria-label="Aerial view of a plunge pool set in a composite deck"/>
    <rect x="623" y="893" width="253" height="138" fill="url(#firepitTones)" role="img" aria-label="Paver patio with lit fire pit seating and a pool"/>

    <polygon class="footer-stone" points="565,1072 933,1072 933,1200 519,1200" fill="var(--stone)"/>
    <polygon class="footer-navy" points="0,1090 562,1090 519,1200 0,1200" fill="var(--navy)"/>
  </svg>

  <div class="brand">
    <div class="brand-name"><span class="brand-mark"></span>SUMMIT BUILDERS</div>
    <div class="brand-tag">OUTDOOR LIVING SPACES</div>
  </div>

  <h1 class="headline">Let’s create<br>your dream<br>outdoor<br>living space!</h1>

  <section class="about">
    <h2 class="section-title">About us</h2>
    <div class="section-rule"></div>
    <p>Discover the endless possibilities for your outdoor space with The Summit Builders Team. Our team of skilled artisans is dedicated to turning your outdoor space into a breathtaking oasis that you’ll love coming home to. Whether it’s a cozy patio for intimate gatherings, a sprawling deck to host memorable parties, or a custom paver driveway that adds instant curb appeal, our high-quality craftsmanship ensures stunning results that exceed your expectations.</p>
  </section>

  <section class="services">
    <h2 class="section-title">Our services</h2>
    <div class="section-rule"></div>
    <ul>
      <li><svg viewBox="0 0 16 16"><circle cx="8" cy="8" r="8" fill="var(--navy)"/><path d="M4.5 8.2l2.3 2.3 4.7-4.8" fill="none" stroke="#fff" stroke-width="2"/></svg>Paver Patios</li>
      <li><svg viewBox="0 0 16 16"><circle cx="8" cy="8" r="8" fill="var(--navy)"/><path d="M4.5 8.2l2.3 2.3 4.7-4.8" fill="none" stroke="#fff" stroke-width="2"/></svg>Paver Driveways</li>
      <li><svg viewBox="0 0 16 16"><circle cx="8" cy="8" r="8" fill="var(--navy)"/><path d="M4.5 8.2l2.3 2.3 4.7-4.8" fill="none" stroke="#fff" stroke-width="2"/></svg>Retaining Walls</li>
      <li><svg viewBox="0 0 16 16"><circle cx="8" cy="8" r="8" fill="var(--navy)"/><path d="M4.5 8.2l2.3 2.3 4.7-4.8" fill="none" stroke="#fff" stroke-width="2"/></svg>Decks &amp; Railings</li>
      <li><svg viewBox="0 0 16 16"><circle cx="8" cy="8" r="8" fill="var(--navy)"/><path d="M4.5 8.2l2.3 2.3 4.7-4.8" fill="none" stroke="#fff" stroke-width="2"/></svg>Pools</li>
      <li><svg viewBox="0 0 16 16"><circle cx="8" cy="8" r="8" fill="var(--navy)"/><path d="M4.5 8.2l2.3 2.3 4.7-4.8" fill="none" stroke="#fff" stroke-width="2"/></svg>Outdoor Lighting</li>
      <li><svg viewBox="0 0 16 16"><circle cx="8" cy="8" r="8" fill="var(--navy)"/><path d="M4.5 8.2l2.3 2.3 4.7-4.8" fill="none" stroke="#fff" stroke-width="2"/></svg>Firepits &amp; Fireplaces</li>
    </ul>
  </section>

  <h2 class="works-title">OUR WORKS</h2>

  <div class="contact-phone">
    <svg viewBox="0 0 24 28"><path d="M6 1l4 6-2.5 2.5c1.2 3.5 3.5 6.5 6.5 8.5L16.5 15.5l6 4-2 5c-1 1.5-3 1.8-5 1C8 22.5 3 15 2 7.5 1.8 5 2.8 3 5 1.5z" fill="#fff"/></svg>
    <span>206-555-0148</span>
  </div>

  <ul class="contact-list">
    <li><svg viewBox="0 0 20 20"><rect x="1" y="4" width="18" height="12" fill="var(--navy)"/><path d="M1.5 4.5l8.5 6.5 8.5-6.5" fill="none" stroke="#cbcbcb" stroke-width="1.6"/></svg>info@summitbuilders.com</li>
    <li><svg viewBox="0 0 20 20" fill="none" stroke="var(--navy)" stroke-width="1.5"><circle cx="10" cy="10" r="8.5"/><ellipse cx="10" cy="10" rx="3.8" ry="8.5"/><path d="M1.5 10h17M3 5.5h14M3 14.5h14"/></svg>www.summitbuilders.com</li>
  </ul>
</main>
</body>
</html>
```